Building technology company seek stationery design and folder design

Letterhead, and a folder design
ideally, I would have two letter head design, one is for one-page bussiness letter. the other one I can use for longer document such report, or analysis regular report page
you can find company logo and overall style at our website:
www.structavolt.example

we are in building technology business, using internet of things technology to improve building energy efficiency to make building greener.

Industry/Entity Type

It Company

Requirements
Must have
• company logo
Nice to have
• techy look abstract graphics, etc.
Should not have
• no comment

```html
<!DOCTYPE html>
<html lang="en">
<head>
<meta charset="utf-8">
<title>StructaVolt Stationery</title>
<link href="https://fonts.googleapis.com/css2?family=Didact+Gothic&family=Questrial&display=swap" rel="stylesheet">
<style>
  :root {
    --backdrop: #dedede;
    --paper: #ffffff;
    --paper-shade: #efefef;
    --brand-green: #b1d44c;
    --brand-green-soft: #bcdb5f;
    --ink: #3a3a3a;
    --ink-soft: #555555;
    --white: #ffffff;
  }
  * { margin: 0; padding: 0; box-sizing: border-box; }
  html, body { width: 1200px; height: 821px; overflow: hidden; background: var(--backdrop); }
  body { position: relative; font-family: "Didact Gothic", "Questrial", sans-serif; color: var(--ink); }

  .letterhead {
    position: absolute; left: 74px; top: 114px; width: 440px; height: 620px;
    background: linear-gradient(90deg, var(--paper) 0%, var(--paper) 30%, var(--paper-shade) 100%);
    box-shadow: 0 1px 3px rgba(0,0,0,.25);
  }
  .letterhead__wordmark {
    position: absolute; top: 82px; left: 0; width: 100%; text-align: center;
    font-family: "Questrial", sans-serif; font-size: 15px; letter-spacing: 2px; color: var(--brand-green);
  }
  .letterhead__wordmark .mark-square {
    display: inline-block; width: 9px; height: 9px; background: var(--brand-green);
    margin-right: 6px; vertical-align: 1px;
  }
  .letter { position: absolute; left: 40px; top: 174px; width: 366px; }
  .letter__salutation { font-size: 11.5px; color: var(--ink); margin-bottom: 18px; }
  .letter__body p { font-size: 5.9px; line-height: 9.6px; color: var(--ink-soft); margin-bottom: 9px; text-align: justify; }
  .letter__closing { font-size: 6px; color: var(--ink-soft); margin-top: 15px; }
  .letter__signature {
    display: block; width: 80px; height: 30px; margin-top: 14px;
    background: linear-gradient(90deg, rgba(177,212,76,.35), rgba(177,212,76,.15));
    border-radius: 3px;
  }
  .letterhead__footer-name {
    position: absolute; right: 40px; bottom: 20px;
    font-family: "Questrial", sans-serif; font-size: 7px; letter-spacing: 1px; color: var(--brand-green);
  }
  .letterhead__footer {
    position: absolute; left: 0; bottom: 0; width: 100%; height: 16px; background: var(--brand-green);
    display: flex; justify-content: center; align-items: center; gap: 8px;
    font-size: 6.2px; color: var(--white);
  }
  .contact { display: inline-flex; align-items: center; gap: 2px; }
  .contact svg { width: 6px; height: 6px; fill: var(--white); }

  .folder {
    position: absolute; left: 553px; top: 77px; width: 519px; height: 658px;
    background: linear-gradient(160deg, var(--brand-green-soft) 0%, var(--brand-green) 60%);
    box-shadow: 0 1px 3px rgba(0,0,0,.25);
  }
  .folder__spine { position: absolute; top: 0; height: 100%; width: 1px; background: rgba(255,255,255,.28); }
  .folder__spine--a { left: 13px; } .folder__spine--b { left: 22px; } .folder__spine--c { left: 31px; }
  .folder__wordmark {
    position: absolute; top: 348px; left: 0; width: 100%; text-align: center;
    font-family: "Questrial", sans-serif; font-size: 30px; letter-spacing: 4px; color: var(--white);
  }
  .folder__wordmark .mark-square {
    display: block; width: 22px; height: 22px; background: var(--white); margin: 0 auto 14px;
  }
</style>
</head>
<body>

<section class="letterhead" aria-label="Letterhead">
  <div class="letterhead__wordmark"><span class="mark-square"></span>STRUCTAVOLT</div>

  <article class="letter">
    <p class="letter__salutation">Dear Mr. Carter,</p>
    <div class="letter__body">
      <p>Our sensor network tracks energy use across every floor and reports each change in real time. This letter outlines the results from your building over the past quarter, along with the steps we propose next. Heating and cooling loads fell steadily after the new controls went live, and lighting schedules now follow actual occupancy rather than fixed hours.</p>
      <p>Peak demand dropped during the warmest weeks, and the chiller plant ran fewer hours than in the same period last year. Our team reviewed the data with your facility staff and agreed on a short list of further tuning tasks. These include new setpoints for the lobby and revised ventilation for the lower levels.</p>
      <p>We will also add sensors to the east wing so that its rooms can join the same control loop. Once installed, the dashboard will show live readings for every zone, and alerts will reach your team when a system drifts outside its normal range. We expect the work to take about three weeks and to cause no disruption to tenants or daily operations in the building.</p>
      <p>Please review the attached summary and let us know a good time to meet. We look forward to helping your building run cleaner and more efficiently in the months ahead.</p>
    </div>
    <p class="letter__closing">Sincerely,</p>
    <span class="letter__signature" role="img" aria-label="Handwritten signature of Dana Carter"></span>
  </article>

  <div class="letterhead__footer-name">STRUCTAVOLT</div>

  <footer class="letterhead__footer">
    <span class="contact">
      <svg viewBox="0 0 10 10"><path d="M2 0.5 L4 2.5 L3 4 Q4.5 6 6 7 L7.5 6 L9.5 8 L8 9.5 Q3.5 9 0.5 2 Z"/></svg>
      (555) 010-4821
    </span>
    <span class="contact">
      <svg viewBox="0 0 10 10"><path d="M0 2 H10 V8.5 H0 Z M0.6 2.4 L5 5.6 L9.4 2.4" stroke="#b1d44c" stroke-width="0.7"/></svg>
      info@structavolt.example
    </span>
    <span class="contact">
      <svg viewBox="0 0 10 10"><circle cx="5" cy="5" r="4.5"/></svg>
      www.structavolt.example
    </span>
    <span class="contact">structavolt</span>
  </footer>
</section>

<section class="folder" aria-label="Presentation folder cover">
  <span class="folder__spine folder__spine--a"></span>
  <span class="folder__spine folder__spine--b"></span>
  <span class="folder__spine folder__spine--c"></span>
  <div class="folder__wordmark"><span class="mark-square"></span>STRUCTAVOLT</div>
</section>

</body>
</html>
```